Design and Renovation Company Luxury Business Card

I want to create a luxury business card for a Design and Renovation Firm . We will use our current logo. The company name is 528BUILDA. We do not want anything standard. We need a very unique concept.
Please see uploaded inspiration. I really like the textured paper option. I would like the card to be thick with debossing, and/or embossing options. The logo has orange in it but I would like to see the card with and without the orange. I think the orange may make the company feel less high-end. The goal is to elevate the logo not match its vibe per se of the logo. We want something very unique, not standard at all!
I would like a space for :
Logo,
Name,
Position,
Email,
Office number,
Website Address,
Business Address,
Thank you!
Have fun!
Target Market(s)
Home owners Age 35 +
Industry/Entity Type
Design and Renovation
Contact Information for Business Card
Logo, Name, Position, Email, Office number, Website Address, Business Address,.
Colors
Designer to choose colors to be used in the design.
Requirements
Must have
- A luxury designer feel. Must be black or dark grey but open to other luxury ideas.
Nice to have
- Gold, silver, black embossing or debossing. Textured paper design.
Should not have
- A cheap look and feel.

```html
<!DOCTYPE html>
<html lang="en">
<head>
<meta charset="utf-8">
<title>528BUILDA Business Card</title>
<link rel="stylesheet" href="https://fonts.googleapis.com/css2?family=Montserrat:wght@400;500;700&display=swap">
<style>
  :root {
    --stage: #d8d3cb;
    --card-light: #ffffff;
    --card-dark: #151515;
    --ink: #111111;
    --ink-soft: #1c1c1c;
    --accent: #f7931e;
    --tile-peach: #fdf3ea;
    --tile-grey: #e6e6e6;
    --paper-white: #ffffff;
  }
  * { margin: 0; padding: 0; box-sizing: border-box; }
  html, body {
    width: 900px; height: 1200px; overflow: hidden;
    background: var(--stage);
    font-family: "Montserrat", sans-serif;
  }
  .canvas { position: relative; width: 900px; height: 1200px; }

  .card {
    position: absolute; left: 80px; width: 742px; height: 440px;
    border-radius: 24px; overflow: hidden;
  }
  .card--front { top: 131px; background: var(--card-light); }
  .card--back { top: 638px; background: var(--card-dark); }

  .tile { position: absolute; }
  .tile--peach { left: 558px; top: 42px; width: 184px; height: 182px; background: var(--tile-peach); }
  .tile--grey-left { left: 341px; top: 257px; width: 183px; height: 183px; background: var(--tile-grey); }
  .tile--grey-right { left: 558px; top: 257px; width: 184px; height: 183px; background: var(--tile-grey); }

  .brand-name { position: absolute; font-weight: 700; line-height: 1; letter-spacing: 0; }
  .card--front .brand-name { left: 44px; top: 74px; font-size: 40px; color: var(--ink); }
  .card--back .brand-name {
    left: 0; right: 0; top: 208px; text-align: center;
    font-size: 60px; color: var(--paper-white);
  }

  .person { position: absolute; left: 34px; top: 256px; color: var(--ink); }
  .person__name { font-size: 27px; font-weight: 700; line-height: 1.1; }
  .person__role { font-size: 17px; font-weight: 400; margin-top: 6px; color: var(--ink-soft); }

  .contacts { position: absolute; left: 34px; top: 330px; list-style: none; }
  .contacts li {
    display: flex; align-items: center; gap: 9px;
    font-size: 17px; color: var(--ink-soft); height: 28px;
  }
  .contacts svg { width: 17px; height: 17px; fill: var(--accent); flex: none; }

  .address {
    position: absolute; left: 494px; top: 370px;
    font-size: 17px; line-height: 20px; color: var(--ink-soft); font-style: normal;
  }
</style>
</head>
<body>
<main class="canvas">
  <section class="card card--front" aria-label="Business card front">
    <div class="tile tile--peach"></div>
    <div class="tile tile--grey-left"></div>
    <div class="tile tile--grey-right"></div>

    <p class="brand-name">528BUILDA</p>

    <div class="person">
      <h1 class="person__name">Adrian Keller</h1>
      <p class="person__role">Managing Director</p>
    </div>

    <ul class="contacts">
      <li>
        <svg viewBox="0 0 24 24" aria-hidden="true"><path d="M6.6 10.8a15.1 15.1 0 0 0 6.6 6.6l2.2-2.2a1 1 0 0 1 1-.25 11.4 11.4 0 0 0 3.6.57 1 1 0 0 1 1 1V20a1 1 0 0 1-1 1A17 17 0 0 1 3 4a1 1 0 0 1 1-1h3.5a1 1 0 0 1 1 1c0 1.25.2 2.45.57 3.57a1 1 0 0 1-.25 1z"/></svg>
        704-555-0148
      </li>
      <li>
        <svg viewBox="0 0 24 24" aria-hidden="true"><path d="M3 6h18v1.2l-9 5.6-9-5.6zM3 9.3l9 5.6 9-5.6V18H3z"/></svg>
        info@528builda.com
      </li>
      <li>
        <svg viewBox="0 0 24 24" aria-hidden="true"><circle cx="12" cy="12" r="9"/></svg>
        www.528builda.com
      </li>
    </ul>

    <address class="address">415 Harbor Oak Ave, #112<br>Lakemont, OH 43210</address>
  </section>

  <section class="card card--back" aria-label="Business card back">
    <p class="brand-name">528BUILDA</p>
  </section>
</main>
</body>
</html>
```